Business Card Design Project

We are a construction company in Orange County, CA. We need a two sided business card. We would like the back to be our logo with web URL. Front should included Name, title, address, phone, fax and email address.

our address is
627 West Dorrance Blvd, Suite 308
Anaheim, CA 92718

Our logo files are attached.

Construction

```html
<!DOCTYPE html>
<html lang="en">
<head>
<meta charset="utf-8">
<title>Braxton Business Card</title>
<link rel="stylesheet" href="https://fonts.googleapis.com/css2?family=Source+Sans+3:wght@400;600;700&display=swap">
<style>
  :root {
    --brand-blue: #124d82;
    --band-grey: #3a3a3c;
    --ink: #333333;
    --card: #ffffff;
    --backdrop: #dcdcdc;
  }
  * { margin: 0; padding: 0; box-sizing: border-box; }
  html, body {
    width: 960px;
    height: 1200px;
    overflow: hidden;
    background: var(--backdrop);
    font-family: "Source Sans 3", "Myriad Pro", Arial, sans-serif;
    color: var(--ink);
  }
  .canvas { position: relative; width: 960px; height: 1200px; }
  .card {
    position: absolute;
    left: 54px;
    width: 840px;
    height: 480px;
    background: var(--card);
    border-radius: 28px;
    overflow: hidden;
  }
  .card--front { top: 66px; }
  .card--back { top: 644px; }

  .wordmark {
    position: absolute;
    color: var(--brand-blue);
    font-weight: 700;
    line-height: 1;
    letter-spacing: -0.01em;
    white-space: nowrap;
  }
  .card--front .wordmark { left: 52px; top: 40px; font-size: 112px; }
  .card--back .wordmark {
    left: 0; right: 0; top: 140px;
    text-align: center;
    font-size: 150px;
  }

  .name-band {
    position: absolute;
    left: 540px;
    top: 232px;
    width: 300px;
    height: 82px;
    display: flex;
  }
  .name-band__label {
    flex: 0 0 254px;
    background: var(--brand-blue);
    color: #fff;
    padding: 12px 0 0 23px;
  }
  .name-band__accent { flex: 1; background: var(--band-grey); }
  .person-name { font-size: 31px; font-weight: 600; line-height: 1; }
  .person-title { font-size: 20px; font-weight: 600; line-height: 1; margin-top: 6px; }

  .contact-list {
    position: absolute;
    left: 563px;
    top: 333px;
    list-style: none;
    font-size: 20px;
    line-height: 33.5px;
  }
  .contact-list b { font-style: italic; font-weight: 700; }

  .address {
    position: absolute;
    left: 45px;
    top: 405px;
    font-size: 21px;
    line-height: 29px;
    font-style: normal;
  }

  .web-url {
    position: absolute;
    left: 0; right: 0; top: 402px;
    text-align: center;
    font-size: 29px;
    font-weight: 700;
  }
</style>
</head>
<body>
<main class="canvas">
  <section class="card card--front" aria-label="Card front">
    <div class="wordmark">BRAXTON</div>
    <div class="name-band">
      <div class="name-band__label">
        <div class="person-name">Your Name</div>
        <div class="person-title">Designation</div>
      </div>
      <div class="name-band__accent"></div>
    </div>
    <ul class="contact-list">
      <li><b>p</b> : 1-234-4567</li>
      <li><b>f</b> &nbsp;: 1-234-4567</li>
      <li><b>e</b> : info@braxtonbuild.com</li>
      <li><b>w</b> : www.braxtonbuild.com</li>
    </ul>
    <address class="address">
      627 West Dorrance Blvd, Suite 308<br>
      Anaheim, CA 92718
    </address>
  </section>

  <section class="card card--back" aria-label="Card back">
    <div class="wordmark">BRAXTON</div>
    <div class="web-url">www.braxtonbuild.com</div>
  </section>
</main>
</body>
</html>
```